Landing Page / Waitlist

I would like a landing page for people to sign up for a waiting list. The text on the page should include (but is not limited to):
1) Main point: The accounting system you'll love
2) Secondary points:
a. Ruthlessly efficient
b. Quietly intelligent
c. Driven by AI
I've attached a file of our logo

The design should be simple, clean, and innovative - this is an ai company

```html
<!DOCTYPE html>
<html lang="en">
<head>
<meta charset="utf-8">
<title>Tallyform — Waitlist</title>
<link rel="stylesheet" href="https://fonts.googleapis.com/css2?family=Outfit:wght@500;600;700&family=Lato:wght@400;700&display=swap">
<style>
  :root {
    --page-bg: #eff0f2;
    --navy-deep: #020c18;
    --navy-mid: #06253f;
    --cyan-glow: #1fb6d9;
    --brand-blue: #0a8ef5;
    --ink: #0b0b0b;
    --muted: #555a60;
    --logo-gray: #808080;
    --white: #ffffff;
    --field-border: #cfd2d6;
  }
  * { box-sizing: border-box; margin: 0; padding: 0; }
  html, body { width: 829px; height: 1200px; overflow: hidden; }
  body { background: var(--page-bg); font-family: "Lato", sans-serif; position: relative; }

  .screen {
    position: absolute; left: 21px; width: 786px; height: 561px;
    overflow: hidden; box-shadow: 0 2px 10px rgba(0,0,0,.12);
  }
  .screen--dark { top: 28px; background: radial-gradient(ellipse 60% 70% at 35% 50%, #0b3552 0%, var(--navy-mid) 35%, var(--navy-deep) 85%); }
  .screen--light { top: 611px; background: var(--white); }

  .brand { position: absolute; display: flex; align-items: center; gap: 8px; font-family: "Outfit", sans-serif; font-weight: 600; }
  .brand__mark { width: 16px; height: 16px; background: var(--brand-blue); }
  .screen--dark .brand { left: 73px; top: 80px; font-size: 32px; color: var(--white); }
  .screen--light .brand { left: 0; right: 0; top: 100px; justify-content: center; font-size: 36px; color: var(--logo-gray); }

  .hero-art { position: absolute; left: 437px; top: 0; width: 349px; height: 520px;
    background: radial-gradient(ellipse 60% 55% at 60% 45%, rgba(31,182,217,.75) 0%, rgba(14,110,150,.45) 45%, rgba(2,12,24,0) 80%); }

  .headline { position: absolute; font-family: "Outfit", sans-serif; font-weight: 600; letter-spacing: -0.5px; }
  .screen--dark .headline { left: 73px; top: 143px; font-size: 45px; line-height: 49px; color: var(--white); }
  .screen--light .headline { left: 0; right: 0; top: 220px; text-align: center; font-size: 35px; line-height: 48px; color: var(--ink); }
  .headline__accent { color: var(--brand-blue); }

  .points { list-style: none; position: absolute; }
  .point { display: flex; align-items: center; }
  .point__dot { width: 10px; height: 10px; border-radius: 50%; background: var(--brand-blue); flex: none; }
  .screen--dark .points { left: 78px; top: 263px; }
  .screen--dark .point { height: 41.5px; gap: 29px; font-size: 17px; font-weight: 700; color: var(--white); }
  .screen--light .points { left: 0; right: 0; top: 287px; display: flex; justify-content: center; gap: 28px; }
  .screen--light .point { gap: 10px; font-size: 16px; color: var(--muted); }

  .waitlist { position: absolute; display: flex; gap: 7px; }
  .screen--dark .waitlist { left: 72px; top: 402px; }
  .screen--light .waitlist { left: 189px; top: 347px; }
  .waitlist__field { height: 38px; border-radius: 5px; border: 1px solid transparent; background: var(--white);
    padding: 0 13px; font-family: "Lato", sans-serif; font-size: 10px; color: var(--muted); }
  .screen--dark .waitlist__field { width: 218px; }
  .screen--light .waitlist__field { width: 274px; border: 1.5px solid var(--field-border); padding-left: 18px; }
  .waitlist__button { width: 120px; height: 38px; border: 0; border-radius: 5px; background: var(--brand-blue);
    color: var(--white); font-family: "Lato", sans-serif; font-weight: 700; font-size: 11px; letter-spacing: -0.2px; }

  .wave-band { position: absolute; left: 0; top: 181px; width: 786px; height: 247px;
    background: linear-gradient(180deg, rgba(255,255,255,0) 0%, rgba(226,214,240,.35) 40%, rgba(214,222,240,.35) 65%, rgba(255,255,255,0) 100%); }

  .footer { position: absolute; left: 0; bottom: 0; width: 100%; height: 41px; background: var(--brand-blue);
    display: flex; align-items: center; justify-content: center; color: var(--white); font-size: 10px; font-weight: 700; }
</style>
</head>
<body>
  <section class="screen screen--dark">
    <div class="hero-art" role="img" aria-label="Glowing cyan circuit-board profile of a head made of binary digits"></div>
    <div class="brand"><span class="brand__mark"></span>Tallyform</div>
    <h1 class="headline">The Accounting<br>System You'll love</h1>
    <ul class="points">
      <li class="point"><span class="point__dot"></span>Ruthlessly efficient</li>
      <li class="point"><span class="point__dot"></span>Quietly intelligent</li>
      <li class="point"><span class="point__dot"></span>Driven by AI</li>
    </ul>
    <form class="waitlist">
      <input class="waitlist__field" type="email" placeholder="Enter Email Address">
      <button class="waitlist__button" type="button">JOIN OUR WAITILST</button>
    </form>
    <footer class="footer">© 2025&nbsp; TALLYFORM. All&nbsp; Rights&nbsp; Reserved</footer>
  </section>

  <section class="screen screen--light">
    <div class="brand"><span class="brand__mark"></span>Tallyform</div>
    <div class="wave-band" role="img" aria-label="Soft flowing lavender wave lines across the page"></div>
    <h1 class="headline">The <span class="headline__accent">Accounting System</span> You'll love</h1>
    <ul class="points">
      <li class="point"><span class="point__dot"></span>Ruthlessly efficient</li>
      <li class="point"><span class="point__dot"></span>Quietly intelligent</li>
      <li class="point"><span class="point__dot"></span>Driven by AI</li>
    </ul>
    <form class="waitlist">
      <input class="waitlist__field" type="email" placeholder="Enter Email Address">
      <button class="waitlist__button" type="button">JOIN OUR WAITILST</button>
    </form>
    <footer class="footer">© 2025 TALLYFORM. All&nbsp; Rights&nbsp; Reserved</footer>
  </section>
</body>
</html>
```